Veterinary Pylon

My veterinary clinic is not clearly visible from the street and I want to place a Pylon next to my driveway. I want a modern, elegant straight Design, the Photo shows the sheduled place. One can see the clinic on our Homepage: www.tailbright-vethaus.at
The last pictures are examples for pylones I like

Target Market(s)

the passing cars often miss my entry...I want to show where to turn left

Colors
3276b5
33a6d7
00a990

Requirements
Must have
• High value, simple elegance, size: 250cm (high) x 100cm (width)
Nice to have
• Our Logo, arrow(?)

A special Text is not necessary but this will be an option:

Biegen sie hier ab und wir biegen es wieder hin!
Should not have
• Too much Color, the colors I have chosen are the possible colors but it‘s not necessary to use them.

```html
<!DOCTYPE html>
<html lang="de">
<head>
<meta charset="utf-8">
<title>Tailbright Vethaus – Pylon</title>
<link rel="stylesheet" href="https://fonts.googleapis.com/css2?family=Archivo+Black&display=swap">
<style>
  :root {
    --brand-navy: #124a91;
    --brand-sky: #2fbde0;
    --ground-tint: #eef9fc;
    --paper: #ffffff;
    --arrow-ink: #ffffff;
  }
  html, body {
    margin: 0;
    padding: 0;
    width: 1200px;
    height: 3000px;
    overflow: hidden;
    background: var(--paper);
  }
  .pylon {
    position: relative;
    width: 1200px;
    height: 3000px;
    overflow: hidden;
    background: var(--paper);
  }
  .pylon__ground {
    position: absolute;
    inset: 0;
    width: 1200px;
    height: 3000px;
  }
  .brand {
    position: absolute;
    left: 0;
    right: 0;
    top: 560px;
    display: flex;
    flex-direction: column;
    align-items: center;
    gap: 22px;
  }
  .brand__mark {
    width: 120px;
    height: 120px;
    border-radius: 50%;
    background: var(--brand-navy);
    margin-bottom: 40px;
  }
  .brand__name {
    margin: 0;
    font-family: "Archivo Black", "Arial Black", sans-serif;
    font-weight: 400;
    color: var(--brand-navy);
    text-transform: uppercase;
    text-align: center;
    line-height: 1;
  }
  .brand__name--primary {
    font-size: 132px;
    letter-spacing: 2px;
  }
  .brand__name--secondary {
    font-size: 96px;
    letter-spacing: 26px;
    padding-left: 26px;
  }
</style>
</head>
<body>
  <main class="pylon">
    <svg class="pylon__ground" viewBox="0 0 1200 3000" aria-hidden="true">
      <path class="ground-band" d="M0 1684 Q600 1380 1200 1690 L1200 3000 L0 3000 Z" fill="var(--ground-tint)"/>
      <path class="ground-arc" d="M0 1684 Q600 1380 1200 1690" fill="none" stroke="var(--brand-sky)" stroke-width="7"/>
      <g class="turn-sign">
        <circle cx="589" cy="1542" r="173" fill="var(--brand-navy)"/>
        <line x1="500" y1="1542" x2="700" y2="1542" stroke="var(--arrow-ink)" stroke-width="19"/>
        <polyline points="569,1460 487,1542 569,1624" fill="none" stroke="var(--arrow-ink)" stroke-width="19"/>
      </g>
    </svg>

    <header class="brand">
      <div class="brand__mark"></div>
      <h1 class="brand__name brand__name--primary">Tailbright</h1>
      <p class="brand__name brand__name--secondary">Vethaus</p>
    </header>
  </main>
</body>
</html>
```